Flyer Design Project

To whom it may concern
Would love the benefit of your expertise

I have a project which is to increase business activity. There are dozens or real estate adds and I want mine to stand out from all others.

My strategy is going with a 50 % sale, what I need is something catchy and something that will make my brochure stand out from the other dozen brochure they have in the mail I need the WOW! Factor

DL Brochure (DL Brochures, Size 99 mm X 210 mm) atm the moment im thinking of only using 1 side but if your design needs both side that is an option

below will be the wording I'm thinking of going with the describe the sale and benefits, i am flexible with the wording if your think something else will sound better

***New Wording***

50% OFF COMMISSION
Sounds good doesn’t it?
Our promise to you from Halvorn Real Estate

List your property with us
And if your buyer has not been found within 15 days
We will slash 50% off our commission!
You will have the benefit of Real Estate consultants
Darren Halvorn and Thomas Velardi
With over 40 years combined experience
Working hard to find your buyer.

Call Today 0491 627 158

Condition Apply

Follow us on Facebook www.facebook.com/tarrowbayhomes

I have attached the link to our website and Facebook page if you want to see a possible color scheme
but i am open to anything

http://brightgatetarrowbay.example.au/
http://www.facebook.com/tarrowbayhomes

Good Luck !!!

Target Market(s)

Home Seller's

Industry/Entity Type

Real Estate

Requirements
Nice to have
• our logo but remember this flyer is not to market our self its to market our offer
so i want to 50% off the stand out not Brightgate Halvorn Real Estate
Should not have
• House in the Background, i would much rather the 50% take up half the page than have the house or even a quirky un related image

```html
<!DOCTYPE html>
<html lang="en">
<head>
<meta charset="utf-8">
<title>50% Off Commission – Halvorn Real Estate</title>
<link rel="stylesheet" href="https://fonts.googleapis.com/css2?family=Oswald:wght@500;700&family=Open+Sans:wght@400;600;700&family=Roboto+Condensed:wght@700&display=swap">
<style>
  :root {
    --backdrop: #3b261b;
    --offer-red: #e31e2a;
    --promise-yellow: #f6bd12;
    --ink: #111111;
    --paper: #ffffff;
    --stripe-green: #2fa84f;
    --stripe-blue: #1d8fd6;
    --photo-light: #eef0f1;
    --photo-mid: #c9ccd0;
    --photo-warm: #a8876f;
  }
  * { box-sizing: border-box; margin: 0; padding: 0; }
  html, body { width: 1200px; height: 2213px; overflow: hidden; }
  body { background: var(--backdrop); position: relative; }

  .flyer {
    position: absolute; left: 133px; top: 135px;
    width: 912px; height: 1943px;
    display: flex; flex-direction: column;
    background: var(--paper);
    overflow: hidden;
  }

  .offer-header {
    height: 509px; flex: none; background: var(--offer-red);
    position: relative; color: var(--paper); overflow: hidden;
  }
  .offer-header__discount,
  .offer-header__commission {
    position: absolute; left: 76px;
    font-family: "Oswald", "Arial Narrow", sans-serif; font-weight: 700;
    line-height: 1; white-space: nowrap;
    text-shadow: 5px 5px 5px rgba(0,0,0,0.55);
  }
  .offer-header__discount { top: 58px; font-size: 190px; letter-spacing: 8px; }
  .offer-header__commission { top: 288px; font-size: 106px; letter-spacing: 19px; }
  .offer-header__tagline {
    position: absolute; left: 150px; top: 406px;
    font-family: "Open Sans", Arial, sans-serif; font-weight: 600;
    font-size: 58px; line-height: 1.2; color: var(--ink); white-space: nowrap;
  }

  .couple-photo {
    height: 708px; flex: none;
    background: linear-gradient(100deg, var(--photo-light) 0%, var(--photo-mid) 45%, var(--photo-warm) 60%, var(--photo-light) 100%);
  }

  .colour-stripe { height: 25px; flex: none; display: flex; }
  .colour-stripe span { display: block; height: 100%; }
  .colour-stripe .red { width: 241px; background: var(--offer-red); }
  .colour-stripe .gap { width: 224px; background: var(--paper); }
  .colour-stripe .green { width: 246px; background: var(--stripe-green); }
  .colour-stripe .blue { flex: 1; background: var(--stripe-blue); }

  .promise-panel {
    height: 315px; flex: none; background: var(--promise-yellow);
    display: flex; align-items: center; padding: 0 30px 0 57px;
  }
  .promise-panel__details {
    width: 520px;
    font-family: "Open Sans", Arial, sans-serif; font-size: 24.5px;
    line-height: 1.33; text-align: justify; color: var(--ink);
  }
  .promise-panel__divider {
    width: 3px; height: 245px; background: var(--paper); margin: 0 26px 0 30px;
  }
  .promise-panel__pledge {
    flex: 1; text-align: center;
    font-family: "Roboto Condensed", "Arial Narrow", sans-serif; font-weight: 700;
    font-size: 40px; line-height: 1.18; color: var(--ink); text-transform: uppercase;
  }

  .brand-bar {
    height: 214px; flex: none; background: var(--paper);
    display: flex; align-items: center; justify-content: center; gap: 26px;
  }
  .brand-bar__mark { width: 64px; height: 64px; background: var(--offer-red); }
  .brand-bar__name {
    font-family: "Open Sans", Arial, sans-serif; font-weight: 700;
    font-size: 92px; color: var(--ink); line-height: 1;
  }

  .call-footer {
    flex: 1; background: var(--offer-red);
    display: flex; flex-direction: column; align-items: center; justify-content: center;
  }
  .call-footer__line {
    color: var(--paper); white-space: nowrap; display: flex; align-items: baseline; gap: 18px;
  }
  .call-footer__prompt { font-family: "Open Sans", Arial, sans-serif; font-weight: 600; font-size: 46px; }
  .call-footer__number { font-family: "Oswald", "Arial Narrow", sans-serif; font-weight: 500; font-size: 70px; line-height: 1; }
  .call-footer__conditions {
    font-family: "Open Sans", Arial, sans-serif; font-size: 22px; color: var(--ink); margin-top: 6px;
  }
</style>
</head>
<body>
  <main class="flyer">
    <header class="offer-header">
      <div class="offer-header__discount">50% OFF</div>
      <div class="offer-header__commission">COMMISSION</div>
      <div class="offer-header__tagline">sounds good doesn’t it?</div>
    </header>

    <div class="couple-photo" role="img" aria-label="Photo of a smiling couple, the woman holding up a set of house keys"></div>

    <div class="colour-stripe" aria-hidden="true">
      <span class="red"></span><span class="gap"></span><span class="green"></span><span class="blue"></span>
    </div>

    <section class="promise-panel">
      <p class="promise-panel__details">List your property with us and if your buyer has not been found within 15 days we will slash 50% off our commission! You will have the benefit of Real Estate consultants Darren Halvorn and Thomas Velardi with over 40 years combined experience working hard to find that buyer for you.</p>
      <div class="promise-panel__divider"></div>
      <p class="promise-panel__pledge">Our<br>promise to<br>you at<br>Halvorn<br>Real Estate</p>
    </section>

    <div class="brand-bar">
      <span class="brand-bar__mark" aria-hidden="true"></span>
      <span class="brand-bar__name">Brightgate</span>
    </div>

    <footer class="call-footer">
      <div class="call-footer__line">
        <span class="call-footer__prompt">Call Thomas Today</span>
        <span class="call-footer__number">0491 627 158</span>
      </div>
      <div class="call-footer__conditions">*Conditions apply*</div>
    </footer>
  </main>
</body>
</html>
```